Property management company looking for modern card design

We at Blue Heron Partners provides property management services for its residential and commercial properties, with expertise in all categories of multifamily, industrial and office projects throughout California.

We need a business card design that is professional and modern designed business card. In our field, clients get hundreds of business cards, we would like our card to stand out.

Please avoid small print.

Target Market(s)

Professionals and high end clients

Industry/Entity Type

Financial Planning

Contact Information for Business Card

Company Name: Blue Heron Partners, Name, email, license #, phone number, website blueheronpartners.com

Font styles to use
Sans Serif

Requirements
Must have
• The card design needs to be adaptable because there is a possibly we will be expanding into different sectors other than real estate. The card design should be focused on financial planning and asset management.
Nice to have
• Modern and simple business card. Eye catching. Non-standard size/shaped cards would be great.
• blueheronpartners.com
Should not have
• Too many bright color or any pictures or shapes of real estate stuff.

```html
<!DOCTYPE html>
<html lang="en">
<head>
<meta charset="utf-8">
<title>Blue Heron Partners – Business Card</title>
<link rel="stylesheet" href="https://fonts.googleapis.com/css2?family=Montserrat:wght@400;500;700&display=swap">
<style>
  :root {
    --backdrop: #ebe8e4;
    --card-dark: #333333;
    --card-light: #ffffff;
    --accent-red: #c9302c;
    --ink: #2b2b2b;
    --ink-soft: #3a3a3a;
    --rule: #9a9a9a;
    --on-dark: #ffffff;
  }
  * { box-sizing: border-box; margin: 0; padding: 0; }
  html, body {
    width: 1200px;
    height: 1000px;
    overflow: hidden;
    background: var(--backdrop);
    font-family: "Montserrat", sans-serif;
  }
  .canvas {
    position: relative;
    width: 1200px;
    height: 1000px;
  }
  .card {
    position: absolute;
    left: 288px;
    width: 625px;
    height: 357px;
    border-radius: 28px;
  }
  .card--front {
    top: 140px;
    background: var(--card-dark);
    display: flex;
    align-items: center;
    justify-content: center;
  }
  .card--back {
    top: 532px;
    background: var(--card-light);
    box-shadow: 0 2px 6px rgba(0,0,0,0.12);
    text-align: center;
  }
  .brand {
    display: flex;
    align-items: center;
    justify-content: center;
    gap: 14px;
  }
  .brand__dot {
    border-radius: 50%;
    background: var(--accent-red);
    flex: none;
  }
  .brand__name {
    font-weight: 400;
    letter-spacing: 1px;
    text-transform: uppercase;
    white-space: nowrap;
  }
  .card--front .brand__dot { width: 40px; height: 40px; }
  .card--front .brand__name { font-size: 34px; color: var(--on-dark); }
  .card--back .brand { padding-top: 52px; gap: 10px; }
  .card--back .brand__dot { width: 28px; height: 28px; }
  .card--back .brand__name { font-size: 25px; color: var(--ink); }
  .holder { margin-top: 84px; }
  .holder__name {
    font-size: 23px;
    font-weight: 700;
    color: var(--accent-red);
    line-height: 1.1;
  }
  .holder__title {
    font-size: 15px;
    font-weight: 500;
    color: var(--ink-soft);
    margin-top: 2px;
  }
  .holder__rule {
    width: 260px;
    height: 2px;
    margin: 12px auto 14px;
    background: linear-gradient(90deg, transparent, var(--rule) 50%, transparent);
  }
  .contact {
    font-size: 15px;
    color: var(--ink);
    line-height: 25px;
    font-weight: 400;
  }
  .contact__label { color: var(--accent-red); }
  .contact__sep { margin: 0 8px; }
</style>
</head>
<body>
<main class="canvas">
  <section class="card card--front" aria-label="Card front">
    <div class="brand">
      <span class="brand__dot" aria-hidden="true"></span>
      <span class="brand__name">Blue Heron Partners</span>
    </div>
  </section>

  <section class="card card--back" aria-label="Card back">
    <div class="brand">
      <span class="brand__dot" aria-hidden="true"></span>
      <span class="brand__name">Blue Heron Partners</span>
    </div>
    <div class="holder">
      <p class="holder__name">Daniel Reyes</p>
      <p class="holder__title">President</p>
      <div class="holder__rule" aria-hidden="true"></div>
    </div>
    <div class="contact">
      <p>License: #7718204</p>
      <p><span class="contact__label">P</span>: 555-2018-4736<span class="contact__sep">|</span><span class="contact__label">E</span>: info@blueheronpartners.com</p>
      <p>www.blueheronpartners.com</p>
    </div>
  </section>
</main>
</body>
</html>
```